Buch-/eBook-Cover für Sachbuch gesucht
Zielgruppe
We're selfpublishing nonfiction books. Interested are adults - mostly man (age range: 25-50) - who want to learn more about leadership at their workplaces.
Aufgabenstellung
The design should be clean and simple, title easy to read, good color contrast (the cover has to stand out from an white background).

```html
<!DOCTYPE html>
<html lang="en">
<head>
<meta charset="utf-8">
<title>Leadership – Book Cover</title>
<link rel="stylesheet" href="https://fonts.googleapis.com/css2?family=Archivo+Black&family=Fira+Sans+Extra+Condensed:wght@500;600&display=swap">
<style>
  :root {
    --paper: #fbfbfa;
    --sky-blue: #2ea3dc;
    --navy: #35336c;
    --accent-red: #cf2230;
    --cloud: #a8dae3;
    --cloud-soft: #c4e6ec;
    --author-teal: #7bc3cf;
    --illustration: #cfe6ee;
  }
  html, body {
    margin: 0;
    padding: 0;
    width: 848px;
    height: 1200px;
    overflow: hidden;
    background: var(--paper);
  }
  .cover {
    position: relative;
    width: 848px;
    height: 1200px;
    background: var(--paper);
    overflow: hidden;
  }
  .cover-art {
    position: absolute;
    inset: 0;
  }
  .title-word {
    font-family: "Archivo Black", "Arial Black", sans-serif;
  }
  .title-light { fill: var(--sky-blue); }
  .title-dark { fill: var(--navy); }
  .subtitle {
    position: absolute;
    left: 119px;
    top: 828px;
    width: 656px;
    margin: 0;
    font-family: "Fira Sans Extra Condensed", "Arial Narrow", sans-serif;
    font-weight: 600;
    font-size: 38px;
    line-height: 46px;
    color: var(--accent-red);
    text-align: right;
    white-space: nowrap;
  }
  .author {
    position: absolute;
    left: 600px;
    top: 898px;
    margin: 0;
    font-family: "Fira Sans Extra Condensed", "Arial Narrow", sans-serif;
    font-weight: 600;
    font-size: 50px;
    line-height: 46px;
    color: var(--author-teal);
    white-space: nowrap;
  }
</style>
</head>
<body>
<main class="cover">
  <svg class="cover-art" width="848" height="1200" viewBox="0 0 848 1200" xmlns="http://www.w3.org/2000/svg">
    <defs>
      <linearGradient id="cloudTone" x1="0" y1="0" x2="0" y2="1">
        <stop offset="0" stop-color="var(--cloud-soft)"/>
        <stop offset="1" stop-color="var(--cloud)"/>
      </linearGradient>
      <linearGradient id="figureTone" x1="0" y1="0" x2="0" y2="1">
        <stop offset="0" stop-color="#e9e3a8"/>
        <stop offset="1" stop-color="#b9cfe0"/>
      </linearGradient>
    </defs>

    <!-- cloud illustration areas -->
    <path d="M35 0 H463 C440 60 380 95 300 100 C220 108 120 112 35 90 Z"
          fill="url(#cloudTone)" role="img" aria-label="Illustration: soft light-blue clouds along the top edge"/>
    <path d="M0 772 C60 772 80 840 110 900 C150 980 220 1040 320 1070 C480 1040 650 1040 848 1055 V1200 H0 Z"
          fill="url(#cloudTone)" role="img" aria-label="Illustration: soft light-blue clouds along the left and bottom edges"/>

    <!-- title -->
    <text class="title-word title-light" x="86" y="392" font-size="286" textLength="518" lengthAdjust="spacingAndGlyphs">LEA</text>
    <text class="title-word title-dark" x="241" y="603" font-size="286" textLength="548" lengthAdjust="spacingAndGlyphs">DER</text>
    <text class="title-word title-light" x="80" y="812" font-size="286" textLength="614" lengthAdjust="spacingAndGlyphs">SHIP</text>

    <!-- figure illustration areas -->
    <rect x="445" y="50" width="100" height="138" fill="url(#figureTone)" opacity=".8" role="img" aria-label="Illustration: business person planting a yellow flag on top of the letter A"/>
    <rect x="598" y="205" width="66" height="186" fill="var(--illustration)" role="img" aria-label="Illustration: two colleagues climbing a rope up the side of the title"/>
    <rect x="129" y="516" width="64" height="84" fill="var(--cloud)" opacity=".7" role="img" aria-label="Illustration: small sprouting plant on top of the letter S"/>
  </svg>

  <p class="subtitle">Fostering Growth and Inspiring Excellence</p>
  <p class="author">Daniel<br>Harwick</p>
</main>
</body>
</html>
```